Business Card Design Project

Doctor, Pain Management. Need a new business card design with appointment info on the back. New address is 18 Corvell Road, Suite 304, Brisdale, NJ 07391. Right now I believe the rest of the information is staying the same.

```html
<!DOCTYPE html>
<html lang="en">
<head>
<meta charset="utf-8">
<title>Gentle Relief Pain Care – Business Card</title>
<link rel="stylesheet" href="https://fonts.googleapis.com/css2?family=Lato:wght@400;700&display=swap">
<style>
:root{
  --orange:#e95c0e;
  --orange-text:#f0691a;
  --night:#0e1317;
  --steel:#6f8495;
  --paper:#efedee;
  --ink:#555a5e;
  --white:#ffffff;
  --backdrop:#e6e3e1;
}
*{box-sizing:border-box;margin:0;padding:0}
html,body{width:1200px;height:1057px;overflow:hidden}
body{background:var(--backdrop);font-family:'Lato',sans-serif;position:relative}
.card{position:absolute;width:602px;height:372px;overflow:hidden;box-shadow:0 6px 18px rgba(0,0,0,.18)}

/* Front */
.card-front{left:162px;top:104px;background:linear-gradient(90deg,#8fa3b3 0%,#5f7384 35%,#1b2329 68%,var(--night) 100%)}
.front-visual{position:absolute;left:0;top:0;width:340px;height:325px;
  background:radial-gradient(ellipse 40% 60% at 40% 62%,rgba(233,92,14,.75),rgba(233,92,14,0) 70%),
             linear-gradient(90deg,#9aacba 0%,#4d5f6e 55%,rgba(27,35,41,0) 100%)}
.front-info{position:absolute;right:30px;top:0;text-align:right;color:var(--white)}
.brand-name{margin-top:52px;color:var(--orange-text);font-weight:400;font-size:44px;line-height:1}
.brand-sub{color:var(--orange-text);font-weight:400;font-size:28px;letter-spacing:3px;line-height:1;margin-top:8px}
.doctor-name{margin-top:40px;color:var(--orange);font-weight:700;font-size:19px}
.doctor-title{font-size:17px;margin-top:2px}
.contact-list{list-style:none;margin-top:12px;font-size:16px}
.contact-list li{display:flex;justify-content:flex-end;align-items:center;gap:6px;height:22px}
.contact-list svg{width:13px;height:13px;fill:var(--orange)}
.address-band{position:absolute;left:0;bottom:0;width:100%;height:47px;background:var(--orange);color:var(--white);
  font-size:16px;display:flex;align-items:center;justify-content:center}

/* Back */
.card-back{left:429px;top:523px;background:var(--paper)}
.appt-head{height:108px;background:var(--orange);color:var(--white);font-size:27px;font-weight:400;letter-spacing:.5px;
  display:flex;align-items:center;justify-content:center;padding-top:6px}
.appt-form{padding:28px 45px 0 52px;color:var(--ink);font-size:19px}
.field-row{display:flex;align-items:baseline;height:37px}
.field-line{flex:1;border-bottom:2px dotted #777;margin:0 4px;height:1px}
.field-short{flex:0 0 152px}
.field-mid{flex:0 0 140px}
.field-gap{margin-left:18px}
.day-row{display:flex;justify-content:space-between;margin-top:14px}
.day{display:flex;align-items:center;gap:6px;font-size:18px}
.day-box{width:23px;height:23px;border:2px solid #6a6e72;background:var(--white)}
.appt-note{position:absolute;left:0;bottom:0;width:100%;height:78px;background:var(--orange);color:var(--white);
  font-size:15px;display:flex;align-items:center;justify-content:center}
</style>
</head>
<body>

<section class="card card-front">
  <div class="front-visual" role="img" aria-label="Illustration of a person's back with the spine highlighted in glowing orange"></div>
  <div class="front-info">
    <p class="brand-name">Gentle Relief</p>
    <p class="brand-sub">PAIN CARE</p>
    <p class="doctor-name">DR. MEILING ZHAO, M.D., PH.D</p>
    <p class="doctor-title">Board Certified Anesthiologist</p>
    <ul class="contact-list">
      <li>973.555.0148 <svg viewBox="0 0 16 16"><path d="M3 5c0-2 1-3 5-3s5 1 5 3l-3 1-1-2H7L6 6zM4 8h8l2 6H2z"/></svg></li>
      <li>973.555.0149 <svg viewBox="0 0 16 16"><rect x="4" y="1" width="8" height="4"/><rect x="1" y="6" width="14" height="6" rx="1"/><rect x="4" y="10" width="8" height="5"/></svg></li>
      <li>www.gentlereliefpc.com <svg viewBox="0 0 16 16"><circle cx="8" cy="8" r="7"/></svg></li>
      <li>reliefcare.office@mailbox.com <svg viewBox="0 0 16 16"><rect x="1" y="3" width="14" height="10"/><path d="M1 3l7 6 7-6" fill="none" stroke="#0e1317" stroke-width="1.4"/></svg></li>
    </ul>
  </div>
  <div class="address-band">18 Corvell Road, Suite 304, Brisdale, NJ 07391</div>
</section>

<section class="card card-back">
  <h2 class="appt-head">APPOINTMENT</h2>
  <div class="appt-form">
    <div class="field-row"><span>Name :</span><span class="field-line"></span></div>
    <div class="field-row">
      <span>Date :</span><span class="field-line field-short"></span>
      <span class="field-gap">Time :</span><span class="field-line field-mid"></span>
      <span>AM / PM</span>
    </div>
    <div class="day-row">
      <span class="day"><span class="day-box"></span>MON</span>
      <span class="day"><span class="day-box"></span>TUE</span>
      <span class="day"><span class="day-box"></span>WED</span>
      <span class="day"><span class="day-box"></span>THU</span>
      <span class="day"><span class="day-box"></span>FRI</span>
      <span class="day"><span class="day-box"></span>SAT</span>
    </div>
  </div>
  <p class="appt-note">If unable to keep your appointment, please contact us as soon as possible</p>
</section>

</body>
</html>
```